Local fast-growing company in the service sector

We are looking for a modern business card design, which should also appear on our letterheads

Target Market(s)

Private and industrial sectors

Contact Information for Business Card

Vorname Name
Kellberger Str. 18
72841 Bergtal
Tel.: 07146-839214-0
Name@agentur-kvtl.de

Colors
9d9d9d
919191
aaaaaa

Requirements
Must have
• The logo (file) in silver

```html
<!DOCTYPE html>
<html lang="de">
<head>
<meta charset="utf-8">
<title>KVTL Visitenkarte</title>
<link href="https://fonts.googleapis.com/css2?family=Source+Sans+3:wght@400;600;700&display=swap" rel="stylesheet">
<style>
  :root {
    --stage: #000000;
    --card-light: #f3f3f3;
    --silver: #9d9d9d;
    --silver-dark: #919191;
    --silver-light: #aaaaaa;
    --ink: #1a1a1a;
    --ink-soft: #333333;
    --white: #ffffff;
  }
  html, body {
    margin: 0;
    width: 1200px;
    height: 900px;
    overflow: hidden;
    background: var(--stage);
    font-family: "Source Sans 3", sans-serif;
  }
  .canvas {
    position: relative;
    width: 1200px;
    height: 900px;
  }
  .card {
    position: absolute;
    top: 200px;
    width: 310px;
    height: 502px;
    box-sizing: border-box;
    overflow: hidden;
  }
  .card--front {
    left: 265px;
    background: var(--card-light);
    border-radius: 50px 0 50px 0;
  }
  .card--back {
    left: 641px;
    width: 309px;
    border-radius: 0 50px 0 50px;
    background: linear-gradient(180deg, #d2d2d2 0%, #b4b4b4 55%, #8e8e8e 100%);
  }
  .brand {
    position: absolute;
    left: 32px;
    top: 86px;
    display: flex;
    align-items: center;
    gap: 14px;
  }
  .brand__mark {
    width: 40px;
    height: 40px;
    background: var(--silver);
  }
  .brand__name {
    font-size: 50px;
    font-weight: 700;
    letter-spacing: 3px;
    color: var(--silver);
    line-height: 1;
  }
  .contact {
    position: absolute;
    left: 29px;
    top: 328px;
    color: var(--ink-soft);
  }
  .contact__name {
    margin: 0 0 14px;
    font-size: 19px;
    font-weight: 600;
    color: var(--ink);
  }
  .contact__address {
    margin: 0 0 20px;
    font-size: 14px;
    line-height: 18px;
    font-style: normal;
  }
  .contact__list {
    list-style: none;
    margin: 0;
    padding: 0;
    font-size: 14px;
    line-height: 18px;
  }
  .contact__list li {
    display: flex;
    align-items: center;
    gap: 7px;
  }
  .contact__icon {
    width: 10px;
    height: 10px;
    fill: var(--ink-soft);
  }
  .back__decor {
    position: absolute;
    inset: 0;
    background:
      linear-gradient(135deg, rgba(255,255,255,0.25) 0%, rgba(255,255,255,0) 45%),
      radial-gradient(ellipse at 55% 60%, rgba(120,120,120,0.25), rgba(120,120,120,0) 60%);
  }
  .back__name {
    position: absolute;
    left: 38px;
    top: 362px;
    margin: 0;
    font-size: 72px;
    font-weight: 700;
    letter-spacing: 6px;
    color: var(--white);
    line-height: 1;
  }
</style>
</head>
<body>
<main class="canvas">
  <section class="card card--front">
    <div class="brand">
      <span class="brand__mark"></span>
      <span class="brand__name">KVTL</span>
    </div>
    <div class="contact">
      <h1 class="contact__name">Vorname Name</h1>
      <address class="contact__address">Kellberger Str. 18<br>72841 Bergtal</address>
      <ul class="contact__list">
        <li>
          <svg class="contact__icon" viewBox="0 0 10 10"><path d="M2 0.5 L3.6 0.5 L4.3 2.8 L3.2 3.7 Q4 5.6 6.3 6.8 L7.2 5.7 L9.5 6.4 L9.5 8 Q9.5 9.5 8 9.5 Q0.5 8.8 0.5 2 Q0.5 0.5 2 0.5 Z"/></svg>
          07146-839214-0
        </li>
        <li>
          <svg class="contact__icon" viewBox="0 0 10 10"><path d="M0.5 2 L9.5 2 L9.5 8.5 L0.5 8.5 Z M1 2.5 L5 5.6 L9 2.5" stroke="#f3f3f3" stroke-width="0.8"/></svg>
          Name@agentur-kvtl.de
        </li>
        <li>
          <svg class="contact__icon" viewBox="0 0 10 10"><circle cx="5" cy="5" r="4.6"/><path d="M0.6 5 H9.4 M5 0.5 Q2.2 5 5 9.5 M5 0.5 Q7.8 5 5 9.5" stroke="#f3f3f3" stroke-width="0.7" fill="none"/></svg>
          www.agentur-kvtl.de
        </li>
      </ul>
    </div>
  </section>

  <section class="card card--back">
    <div class="back__decor" role="img" aria-label="Große silberne Markenornamentik als Hintergrund"></div>
    <p class="back__name">KVTL</p>
  </section>
</main>
</body>
</html>
```